Design for schnapps bottle label "Río Ámbar"

Hi! On a small land lot we are producing our own Italian schnapps "Grappa". For the bottles we would like to modernize our current labes that you find below. The two cats looking at each other should remain, but updated and more modern. I am very much looking forward to your suggestions. Best, Jens

Target Market(s)

Schnapps bottle label

Requirements
Must have
• Cats should resemble the cats that are decorating the house entry (see attached), however, should have a more modern appearance.

Text elements should remain: "Grappa", "Río Ámbar", "Legnoso", "[Vintage Year], "Raccolta No", "Vol %"
Should not have
• Current ornament can be used, replaced or deleted (whatever looks best)

```html
<!DOCTYPE html>
<html lang="it">
<head>
<meta charset="utf-8">
<title>Grappa di Río Ámbar — Etichetta Legnoso 2015</title>
<link href="https://fonts.googleapis.com/css2?family=Cinzel:wght@400&family=Great+Vibes&display=swap" rel="stylesheet">
<style>
  :root {
    --backdrop: #e2e2e2;
    --label-paper: #ffffff;
    --ink: #0d0d0d;
    --band-ink: #ffffff;
    --art-light: #f4f4f4;
    --art-dark: #111111;
  }
  html, body {
    margin: 0;
    padding: 0;
    width: 838px;
    height: 1200px;
    overflow: hidden;
    background: var(--backdrop);
  }
  .label {
    position: absolute;
    left: 119px;
    top: 97px;
    width: 600px;
    height: 1006px;
    background: var(--label-paper);
    color: var(--ink);
    font-family: "Cinzel", serif;
    text-align: center;
    box-shadow: 0 2px 10px rgba(0,0,0,0.08);
  }
  .label__title {
    position: absolute;
    top: 62px;
    left: 0;
    right: 0;
    margin: 0;
    font-size: 78px;
    font-weight: 400;
    letter-spacing: 2px;
    line-height: 1;
  }
  .label__connector {
    position: absolute;
    top: 208px;
    left: 0;
    right: 0;
    font-size: 20px;
    letter-spacing: 1px;
  }
  .label__brand {
    position: absolute;
    top: 300px;
    left: 0;
    right: 0;
    font-family: "Great Vibes", cursive;
    font-size: 104px;
    line-height: 1;
  }
  .label__art {
    position: absolute;
    top: 450px;
    left: 0;
    width: 600px;
    height: 378px;
    background: linear-gradient(to bottom, var(--art-light) 0%, var(--art-light) 30%, #6a6a6a 70%, var(--art-dark) 100%);
  }
  .label__variety {
    position: absolute;
    top: 484px;
    left: 0;
    right: 0;
    font-size: 33px;
    line-height: 1.25;
    letter-spacing: 1px;
  }
  .label__band {
    position: absolute;
    left: 0;
    bottom: 0;
    width: 600px;
    height: 178px;
    background: var(--ink);
    color: var(--band-ink);
    font-size: 26px;
    letter-spacing: 1px;
    line-height: 54px;
    padding-top: 34px;
    box-sizing: border-box;
  }
  .label__band p { margin: 0; }
</style>
</head>
<body>
  <main class="label">
    <h1 class="label__title">GRAPPA</h1>
    <div class="label__connector">DI</div>
    <div class="label__brand">Río Ámbar</div>
    <div class="label__art" role="img" aria-label="Illustrazione di due gatti neri stilizzati che si stirano uno di fronte all'altro, con le code arricciate"></div>
    <div class="label__variety">
      <div>LEGNOSO</div>
      <div>2015</div>
    </div>
    <footer class="label__band">
      <p>RACCOLTA NO.01</p>
      <p>41.0% VOL. 70 CL</p>
    </footer>
  </main>
</body>
</html>
```